AI Business Tools Landing Page

My web-based website builder (Pavlora.com) will be adding many new features in the very near future and I need an eye-catching landing page to promote these new products.

The page will have a primary section of the 8 main products we are promoting:
1. AI Instant Website Generator
2. AI Chatbot
3. Online Store Builder with AI Assistance
4. AI Auto-Blogging System
5. Online Scheduling System
6. Custom Email System
7. SEO Service
8. CRM System

The page will also have a smaller section for links to our affiliate programs. These can be smaller, less-promanent buttons or links. These are the affiliate products:
1. Get Your LLC
2. Website Design and Maintenance
3. Searchly Ads Management
4. Social Media Posting Service
5. Logo Design
6. Trademark Registration
7. Patent Application
8. Printing Services (including postcards, flyers, and merch.)
9. Bulk AI Content Generator

The theme and color scheme of the page should follow the theme of our main website, which is https://pavlora.com.

I need the page fully coded and ready to deploy on my server.

I look forward to seeing your amazing designs!

```html
<!DOCTYPE html>
<html lang="en">
<head>
<meta charset="utf-8">
<title>Pavlora – AI Website Builder</title>
<link href="https://fonts.googleapis.com/css2?family=Poppins:wght@300;400;500;600;700&family=Lato:wght@400&family=Inter:wght@400;500&display=swap" rel="stylesheet">
<style>
:root{
  --brand:#1592e2;
  --brand-deep:#0a6fd6;
  --brand-light:#3fa6ea;
  --navy:#1f2d4a;
  --hero-dark:#0b1a45;
  --hero-mid:#13348a;
  --text:#2a3550;
  --muted:#5a6275;
  --line:#e3e6ee;
  --footer:#0d1b3d;
  --white:#ffffff;
}
*{margin:0;padding:0;box-sizing:border-box}
html,body{width:1200px;height:2682px;overflow:hidden;background:var(--white)}
body{position:relative;font-family:"Poppins",sans-serif;color:var(--text)}

.site-header{position:absolute;left:0;top:0;width:1200px;height:73px;background:var(--white);border-bottom:1px solid var(--line)}
.brand{position:absolute;left:92px;top:20px;display:flex;align-items:center;gap:10px;font-family:"Poppins",sans-serif;font-weight:600;font-size:25px;color:var(--navy)}
.brand-mark{width:34px;height:34px;border-radius:50%;background:var(--brand)}
.main-nav{position:absolute;left:365px;top:27px;display:flex;gap:25px;font-family:"Inter",sans-serif;font-size:15px;color:var(--navy)}
.btn-header{position:absolute;left:1004px;top:15px;width:144px;height:42px;border-radius:6px 0 6px 0;background:var(--brand);color:var(--white);font-family:"Inter",sans-serif;font-size:15px;display:flex;align-items:center;justify-content:center}

.hero-art{position:absolute;left:0;top:73px}
.hero-copy{position:absolute;left:143px;top:180px;width:480px;color:var(--white)}
.hero-title{font-weight:300;font-size:42px;line-height:52px}
.hero-title strong{font-weight:600}
.hero-title .accent{font-weight:700}
.hero-text{margin-top:18px;font-family:"Lato",sans-serif;font-size:17.5px;line-height:25px}
.btn-hero{position:absolute;left:147px;top:459px;width:157px;height:46px;border-radius:8px 0 8px 0;background:var(--brand);color:var(--white);font-family:"Inter",sans-serif;font-size:18px;display:flex;align-items:center;justify-content:center}

.section-head{position:absolute;left:0;width:1200px;text-align:center}
.section-title{font-weight:400;font-size:40px;line-height:50px}
.section-title strong{font-weight:600}
.section-sub{margin-top:10px;font-family:"Lato",sans-serif;font-size:18.5px}
.section-rule{width:110px;height:2px;margin:22px auto 0}
.products-head{top:830px;color:var(--navy)}
.products-head .section-sub{color:var(--muted)}
.products-head .section-rule{background:var(--brand)}

.product-card{position:absolute;width:296px;height:250px;background:var(--white);border:1px solid var(--line);border-radius:4px;box-shadow:0 2px 6px rgba(30,50,90,.08);padding:34px 28px 0 29px}
.product-card.is-active{background:var(--brand);border-color:var(--brand);color:var(--white);height:248px}
.product-icon{width:82px;height:62px;display:block}
.product-name{margin-top:18px;font-weight:600;font-size:19px;line-height:22px;color:var(--navy)}
.product-desc{margin-top:12px;font-family:"Inter",sans-serif;font-size:15px;line-height:21px;color:var(--muted)}
.is-active .product-name,.is-active .product-desc{color:var(--white)}
.product-card.is-add{display:flex;align-items:center;justify-content:center;padding:0}

.affiliate-bg{position:absolute;left:0;top:1940px}
.affiliate-head{top:2092px;color:var(--white)}
.affiliate-head .section-rule{background:var(--white)}
.affiliate-grid{position:absolute;left:267px;top:2237px;display:grid;grid-template-columns:repeat(3,211px);grid-auto-rows:80px;gap:17px 17px}
.affiliate-link{background:var(--brand-light);border-radius:6px;color:var(--white);font-size:16px;line-height:20px;text-align:center;display:flex;align-items:center;justify-content:center;padding:0 30px;text-decoration:none}

.site-footer{position:absolute;left:0;top:2610px;width:1200px;height:72px;background:var(--footer);color:#8b93a8;font-family:"Inter",sans-serif;font-size:16px;display:flex;align-items:center;justify-content:center}
</style>
</head>
<body>

<header class="site-header">
  <div class="brand"><span class="brand-mark"></span>Pavlora</div>
  <nav class="main-nav"><span>About Us</span><span>Learn More</span><span>Make Money</span><span>History of AI</span><span>Pricing</span><span>Blog</span></nav>
  <a class="btn-header">Get Started</a>
</header>

<svg class="hero-art" width="1200" height="715" viewBox="0 0 1200 715" role="img" aria-label="Illustration of a person at a computer with a glowing digital network face outline">
  <defs>
    <linearGradient id="heroGrad" x1="0" y1="0" x2="1" y2="1">
      <stop offset="0" stop-color="#14316f"/>
      <stop offset=".55" stop-color="#0c1f55"/>
      <stop offset="1" stop-color="#1a47a8"/>
    </linearGradient>
    <radialGradient id="heroGlow" cx=".72" cy=".38" r=".35">
      <stop offset="0" stop-color="#2a6fd0" stop-opacity=".55"/>
      <stop offset="1" stop-color="#2a6fd0" stop-opacity="0"/>
    </radialGradient>
  </defs>
  <polygon points="0,0 1200,0 1200,467 1118,512 1108,557 410,712 140,552 115,552 0,467" fill="var(--brand)"/>
  <polygon points="0,0 1200,0 1200,455 1110,500 1100,545 410,708 150,540 115,540 0,455" fill="url(#heroGrad)"/>
  <polygon points="0,0 1200,0 1200,455 1110,500 1100,545 410,708 150,540 115,540 0,455" fill="url(#heroGlow)"/>
</svg>

<div class="hero-copy">
  <h1 class="hero-title">Create a website<br>with <strong>Pavlora</strong><br><span class="accent">AI Website Builder</span></h1>
  <p class="hero-text">Northwind Advisory provides decades of experience implementing Ledgerline EPM products with unique and innovative solutions to challenging business...</p>
</div>
<a class="btn-hero">Get Started</a>

<div class="section-head products-head">
  <h2 class="section-title">Our <strong>Products</strong></h2>
  <p class="section-sub">Lorem Ipsum is simply dummy text of the printing and typesetting industry.</p>
  <div class="section-rule"></div>
</div>

<article class="product-card" style="left:133px;top:1043px">
  <svg class="product-icon" viewBox="0 0 82 62"><circle cx="58" cy="36" r="22" fill="#e6e9f1"/><circle cx="32" cy="32" r="16" fill="none" stroke="var(--brand)" stroke-width="2.5"/><circle cx="32" cy="32" r="6" fill="none" stroke="var(--brand)" stroke-width="2.5"/></svg>
  <h3 class="product-name">AI Instant Website Generator</h3>
  <p class="product-desc">Lorem Ipsum is simply dummy text of the printing</p>
</article>

<article class="product-card is-active" style="left:453px;top:1004px">
  <svg class="product-icon" viewBox="0 0 82 62"><rect x="1" y="2" width="52" height="44" rx="3" fill="none" stroke="#fff" stroke-width="2.5"/><line x1="27" y1="46" x2="27" y2="56" stroke="#fff" stroke-width="2.5"/><line x1="15" y1="56" x2="39" y2="56" stroke="#fff" stroke-width="2.5"/><path d="M20 18l-6 6 6 6M34 18l6 6-6 6M30 15l-6 18" fill="none" stroke="#fff" stroke-width="2.5"/></svg>
  <h3 class="product-name">AI Chatbot</h3>
  <p class="product-desc">Lorem Ipsum is simply dummy text of the printing</p>
</article>

<article class="product-card" style="left:771px;top:1043px">
  <svg class="product-icon" viewBox="0 0 82 62"><circle cx="58" cy="30" r="22" fill="#e6e9f1"/><circle cx="34" cy="18" r="8" fill="none" stroke="var(--brand)" stroke-width="2.5"/><path d="M14 44l14-10h14l14 10-14 12H28z" fill="none" stroke="var(--brand)" stroke-width="2.5"/></svg>
  <h3 class="product-name">Online Store Builder with AI Assistance</h3>
  <p class="product-desc">Lorem Ipsum is simply dummy text of the printing</p>
</article>

<article class="product-card" style="left:133px;top:1320px">
  <svg class="product-icon" viewBox="0 0 82 62"><circle cx="58" cy="30" r="22" fill="#e6e9f1"/><rect x="5" y="2" width="38" height="54" rx="4" fill="none" stroke="var(--brand)" stroke-width="2.5"/><path d="M13 16h22M13 26h22M13 36h14M30 46l6 6 14-16" fill="none" stroke="var(--brand)" stroke-width="2.5"/></svg>
  <h3 class="product-name">AI Auto-Blogging System</h3>
  <p class="product-desc">Lorem Ipsum is simply dummy text of the printing</p>
</article>

<article class="product-card" style="left:453px;top:1279px">
  <svg class="product-icon" viewBox="0 0 82 62"><circle cx="58" cy="30" r="22" fill="#e6e9f1"/><rect x="18" y="20" width="16" height="16" rx="2" fill="none" stroke="var(--brand)" stroke-width="2.5"/><g fill="none" stroke="var(--brand)" stroke-width="2.5"><circle cx="10" cy="10" r="5"/><circle cx="42" cy="10" r="5"/><circle cx="10" cy="46" r="5"/><circle cx="42" cy="46" r="5"/><path d="M14 14l5 6M38 14l-5 6M14 42l5-6M38 42l-5-6"/></g></svg>
  <h3 class="product-name">Online Scheduling System</h3>
  <p class="product-desc">Lorem Ipsum is simply dummy text of the printing</p>
</article>

<article class="product-card" style="left:771px;top:1320px">
  <svg class="product-icon" viewBox="0 0 82 62"><circle cx="58" cy="30" r="22" fill="#e6e9f1"/><rect x="1" y="2" width="56" height="40" rx="3" fill="none" stroke="var(--brand)" stroke-width="2.5"/><path d="M8 12h40M8 22h40M8 32h40M29 42v10M18 54h22" fill="none" stroke="var(--brand)" stroke-width="2.5"/></svg>
  <h3 class="product-name">Custom Email System</h3>
  <p class="product-desc">Lorem Ipsum is simply dummy text of the printing</p>
</article>

<article class="product-card" style="left:133px;top:1596px">
  <svg class="product-icon" viewBox="0 0 82 62"><circle cx="58" cy="36" r="22" fill="#e6e9f1"/><circle cx="30" cy="24" r="19" fill="none" stroke="var(--brand)" stroke-width="2.5"/><path d="M16 38L4 52" stroke="var(--brand)" stroke-width="4"/></svg>
  <h3 class="product-name">SEO Service</h3>
  <p class="product-desc">Lorem Ipsum is simply dummy text of the printing</p>
</article>

<article class="product-card" style="left:453px;top:1555px">
  <svg class="product-icon" viewBox="0 0 82 62"><circle cx="58" cy="36" r="22" fill="#e6e9f1"/><circle cx="28" cy="22" r="18" fill="none" stroke="var(--brand)" stroke-width="2.5"/><circle cx="28" cy="22" r="7" fill="none" stroke="var(--brand)" stroke-width="2.5"/><rect x="6" y="38" width="44" height="16" rx="3" fill="#fff" stroke="var(--brand)" stroke-width="2.5"/></svg>
  <h3 class="product-name">CRM System</h3>
  <p class="product-desc">Lorem Ipsum is simply dummy text of the printing</p>
</article>

<div class="product-card is-add" style="left:771px;top:1596px">
  <svg width="124" height="124" viewBox="0 0 124 124"><path d="M62 0v124M0 62h124" stroke="#c9cdd6" stroke-width="1.5"/></svg>
</div>

<svg class="affiliate-bg" width="1200" height="670" viewBox="0 0 1200 670">
  <polygon points="0,245 115,158 140,158 410,8 1110,155 1122,205 1200,250 1200,670 0,670" fill="var(--brand-deep)"/>
  <polygon points="0,260 120,175 145,175 410,0 1100,160 1112,212 1200,262 1200,670 0,670" fill="var(--brand)"/>
</svg>

<div class="section-head affiliate-head">
  <h2 class="section-title">Affiliate <strong>Products</strong></h2>
  <p class="section-sub">Lorem Ipsum is simply dummy text of the printing and typesetting industry.</p>
  <div class="section-rule"></div>
</div>

<nav class="affiliate-grid">
  <a class="affiliate-link">Get Your LLC</a>
  <a class="affiliate-link">Website Design and Maintenance</a>
  <a class="affiliate-link">Searchly Ads Management</a>
  <a class="affiliate-link">Social Media Posting Service</a>
  <a class="affiliate-link">Logo Design</a>
  <a class="affiliate-link">Trademark Registration</a>
  <a class="affiliate-link">Patent Application</a>
  <a class="affiliate-link">Printing Services</a>
  <a class="affiliate-link">Bulk AI Content Generator</a>
</nav>

<footer class="site-footer">Copyright © pavlora 2024. All rights reserved. | Privacy Policy</footer>

</body>
</html>
```